Velvet Harbor Snout Sticks - our own unique product line of cotton swabs

We have something now that we are not too happy with. Looking to create a label for a line of cotton swabs that we have created and designed to clean your nose from mucus and boogers. The logo that i have so far for the packaging is the white background with the black silhouette nose (attached). We need something that can do well in the retail/consumer market. Our website address (even though it is not live yet) should be listed somewhere on the label....
www.VelvetHarborGoods.example ( we sell pillows, but we have other product lines)
We would also like to see a brief description on how to correctly use the nose pick on the back side of the label. The description on how to use should read " insert cotton nose pick into nostril and give it a few counter clock wise twirls or till you feel mucus/debris latch onto the cotton. You may need to repeat the process and use more than one nose pick to achieve desired result."
As well as a warning mentioning : "Never insert plastic end of nose pick into any part of your body. Be careful and use with caution."
Also for you to know, the cotton is made from 100% natural cotton, the cotton head itself is thick and highly absorbent making it a pleasure to use. There are 50 nose picks per pack.
We're fine with keeping it simple and not making the packaging too busy, however we're open to your ideas and designs! I have given you the most important information relevant to the project. If there are any questions or something is not clear enough please kindly message me.

Requirements
Must have
• professional looking
clean looking
not busy
Should not have
• words clumping together making it appear as too much text in one area
too much text clumped together on the design

```html
<!DOCTYPE html>
<html lang="en">
<head>
<meta charset="utf-8">
<title>Velvet Harbor Snout Sticks – Cotton Swabs Label</title>
<link href="https://fonts.googleapis.com/css2?family=Montserrat:wght@600;700;800&display=swap" rel="stylesheet">
<style>
  :root {
    --page: #eef0f1;
    --label: #ffffff;
    --ink-grey: #6c737a;
    --logo-grey: #7d858b;
    --teal: #1e9e95;
    --teal-light: #9ad8d2;
    --teal-seal: #5fbcb4;
    --band-grey-dark: #6d757b;
    --band-grey-light: #c9cdd0;
    --art-light: #f3f4f5;
    --art-mid: #dfe2e4;
  }
  * { margin: 0; padding: 0; box-sizing: border-box; }
  html, body { width: 1200px; height: 1197px; overflow: hidden; background: var(--page); }
  body { font-family: "Montserrat", sans-serif; position: relative; }

  .label {
    position: absolute; left: 60px; top: 160px; width: 1080px; height: 880px;
    background: var(--label); border-radius: 6px; overflow: hidden;
    box-shadow: 0 10px 40px rgba(0,0,0,0.08);
  }

  .nose-art {
    position: absolute; left: 90px; top: 120px; width: 110px; height: 260px;
    background: linear-gradient(180deg, var(--art-light), var(--art-mid));
    border-radius: 50px 10px 40px 20px;
  }

  .brand { position: absolute; left: 230px; top: 170px; color: var(--logo-grey); font-weight: 600; }
  .brand-name { font-size: 62px; line-height: 1; letter-spacing: -0.5px; white-space: nowrap; }
  .brand-line { font-size: 26px; letter-spacing: 9px; margin-top: 22px; padding-top: 16px; border-top: 4px solid var(--logo-grey); width: 430px; white-space: nowrap; }

  .seal { position: absolute; left: 760px; top: 90px; width: 220px; height: 220px; }

  .claim {
    position: absolute; left: 90px; top: 440px; white-space: nowrap;
    font-size: 46px; font-weight: 700; color: var(--ink-grey); letter-spacing: 3px;
  }

  .title-band {
    position: absolute; left: 40px; right: 0; top: 520px; height: 140px;
    background: linear-gradient(90deg, var(--teal-light), var(--teal) 75%);
    z-index: 1;
  }
  .title {
    position: absolute; left: 90px; top: 538px; white-space: nowrap; z-index: 3;
    font-size: 80px; font-weight: 800; color: #fff; letter-spacing: 1px; line-height: 1.1;
  }

  .tagline-band {
    position: absolute; left: 40px; width: 760px; top: 650px; height: 66px; z-index: 2;
    background: linear-gradient(90deg, var(--band-grey-light), var(--band-grey-dark) 60%);
    display: flex; align-items: center; padding-left: 50px;
  }
  .tagline { font-size: 23px; font-weight: 700; color: #fff; letter-spacing: 1px; white-space: nowrap; }

  .swab-art {
    position: absolute; left: 820px; top: 400px; width: 100px; height: 440px; z-index: 4;
    background: linear-gradient(180deg, var(--art-light), var(--art-mid));
    border-radius: 50px; opacity: 0.85;
  }

  .count {
    position: absolute; right: 24px; top: 545px; z-index: 5;
    color: #fff; font-weight: 700; text-align: center; line-height: 1;
  }
  .count-num { font-size: 64px; }
  .count-unit { font-size: 30px; margin-top: 4px; }

  .url {
    position: absolute; left: 90px; top: 770px; white-space: nowrap;
    font-size: 32px; font-weight: 700; color: var(--teal); letter-spacing: 1px;
  }
</style>
</head>
<body>
  <main class="label">
    <div class="nose-art" role="img" aria-label="Line drawing of a nose in profile"></div>

    <div class="brand">
      <div class="brand-name">Velvet Harbor</div>
      <div class="brand-line">Snout Sticks</div>
    </div>

    <svg class="seal" viewBox="0 0 220 220" role="img" aria-label="Natural cotton, highly absorbent seal with cotton flower">
      <circle cx="110" cy="110" r="108" fill="var(--teal-seal)"/>
      <circle cx="110" cy="110" r="48" fill="#dff1ef"/>
    </svg>

    <div class="claim">100% NATURAL COTTON</div>

    <div class="title-band"></div>
    <h1 class="title">COTTON SWABS</h1>

    <div class="tagline-band"><p class="tagline">CLEAN YOUR NOSE FROM MUCUS AND BOOGERS</p></div>

    <div class="swab-art" role="img" aria-label="Two crossed cotton swabs drawn in outline"></div>

    <div class="count"><div class="count-num">50</div><div class="count-unit">units</div></div>

    <p class="url">www.VelvetHarborGoods.example</p>
  </main>
</body>
</html>
```